Glazorra Donut shop that needs branding like the joy it serves

we need a vibrant and aesthetic design for our packaging boxes/bags,

once approved we will further move to the merchandise, e.t.c

we are bringing the trend of donuts in Pakistan and have started an all out competition in the country for donuts, we provide quality donuts and now we need a design to go along with it to sell, we want it to be vibrant, aesthetically pleasing and cost effective as well so we can target the masses, the final design should give an idea of relativity and aesthetically pleasing and attractive while representing how we are quality focused and are here for everyone,

glazorra donuts, please check the instagram and facebook handle to get a better idea of what we need,

https://www.pastrybook.example/search/top?q=glazorra%20donuts

https://www.snapgram.example/glazorradonuts/

we would like to use white background, with the use of pink black and yellow (modification are also welcome)

a bit graffiti style but decent

i am providing some referal images so you can have an idea

we use lines:
Share a moment of joy
spreading joy

box of joy

here are the sizes required, and the pictures of current boxes are attached
box of 4:

length: 8"
width: 8"
height: 2.25"

inches

box of 8:
length: 16"
width: 8"
height: 2.25"

box of 6:

length: 12"
width: 8"
height: 2.25"

box of 12:

length: 16"
width: 12"
height: 2.25"

packet

height: 9.5"
base: 4"
width: 5.5"

(there's also room for design for special occasions)
(and for marketing giveaways on the box of four that says something delightful and looks appealing)

the box design to be followed is also provided in the picture
(black box)

every gender and age

donut shop

Designer to choose colors to be used in the design.

• creativity and decency

```html
<!DOCTYPE html>
<html lang="en">
<head>
<meta charset="utf-8">
<title>Glazorra Donuts – Box Packaging</title>
<link rel="stylesheet" href="https://fonts.googleapis.com/css2?family=Permanent+Marker&family=Poppins:ital,wght@0,700;0,800;1,400&display=swap">
<style>
  :root {
    --bg: #ebebeb;
    --black: #0b0b0b;
    --pink: #e8325c;
    --pink-soft: #f08aa4;
    --yellow: #f9c118;
    --white: #ffffff;
  }
  * { box-sizing: border-box; margin: 0; padding: 0; }
  html, body { width: 1200px; height: 1200px; overflow: hidden; background: var(--bg); }
  .canvas { position: relative; width: 1200px; height: 1200px; }

  .side-panel {
    position: absolute; left: 110px; top: 250px; width: 160px; height: 700px;
    background: var(--black); color: var(--white);
  }
  .side-brand {
    position: absolute; top: 40px; left: 50%; transform: translateX(-50%);
    writing-mode: vertical-rl;
    display: flex; align-items: center; gap: 14px;
  }
  .side-brand .dot { width: 44px; height: 44px; border-radius: 50%; background: var(--pink); }
  .side-brand .name { font: 800 30px "Poppins", sans-serif; color: var(--yellow); }
  .side-info {
    position: absolute; bottom: 50px; left: 50%; transform: translateX(-50%);
    writing-mode: vertical-rl;
    font: italic 400 18px/1.5 "Poppins", sans-serif; color: var(--white);
  }
  .side-info .handle { margin-right: 14px; display: flex; align-items: center; gap: 10px; }
  .side-info .handle .dot { width: 18px; height: 18px; border: 2px solid var(--white); border-radius: 50%; }

  .front-panel {
    position: absolute; left: 270px; top: 250px; width: 820px; height: 700px;
    overflow: hidden;
  }
  .pattern-field {
    position: absolute; inset: 0;
    background:
      radial-gradient(circle at 15% 20%, var(--yellow) 0 12%, transparent 22%),
      radial-gradient(circle at 80% 75%, var(--yellow) 0 10%, transparent 20%),
      radial-gradient(circle at 70% 25%, var(--pink-soft) 0 14%, transparent 26%),
      radial-gradient(circle at 25% 80%, var(--pink-soft) 0 14%, transparent 26%),
      linear-gradient(135deg, var(--pink) 0%, var(--black) 35%, var(--pink) 60%, var(--black) 100%);
  }
  .brand-badge {
    position: absolute; left: 330px; top: 120px; width: 200px; height: 200px;
    border-radius: 50%; background: var(--black);
    display: flex; align-items: center; justify-content: center;
  }
  .brand-badge .name { font: 800 34px "Poppins", sans-serif; color: var(--yellow); }
  .tagline {
    position: absolute; left: 90px; top: 390px; width: 720px;
    transform: rotate(-14deg); transform-origin: center;
    font: 400 76px/0.95 "Permanent Marker", cursive;
    color: var(--white); text-align: center; letter-spacing: 1px;
    text-shadow: 3px 3px 0 var(--black), -3px -3px 0 var(--black), 3px -3px 0 var(--black),
                 -3px 3px 0 var(--black), 7px 7px 0 var(--black);
  }
  .tagline .line-2 { display: block; padding-left: 120px; }
</style>
</head>
<body>
<main class="canvas">
  <section class="side-panel">
    <div class="side-brand">
      <span class="dot"></span>
      <span class="name">Glazorra</span>
    </div>
    <div class="side-info">
      <p class="address">Noor Plaza Green Avenue<br>Islamabad</p>
      <p class="handle"><span class="dot"></span>glazorradonuts</p>
    </div>
  </section>

  <section class="front-panel">
    <div class="pattern-field" role="img" aria-label="Geometric tile pattern of pink, yellow, black and white squares, quarter circles and donut rings"></div>
    <div class="brand-badge"><span class="name">Glazorra</span></div>
    <h1 class="tagline">SHARE A MOMENT<span class="line-2">OF JOY!</span></h1>
  </section>
</main>
</body>
</html>
```